Business Card Design for Software Development Company

I am looking for a business card design the incorporates my new logo (attached below).

Key information to include:
Name: Martin Quelbrook
Title: CEO
Email: martin@brightwellcivic.example
Phone: 555-218-9403
Website: www.brightwellcivic.example

NOTE: This design should be easy to edit so that we can order cards for different members of our team.

```html
<!DOCTYPE html>
<html lang="en">
<head>
<meta charset="utf-8">
<title>BrightwellLabs Business Card</title>
<link rel="stylesheet" href="https://fonts.googleapis.com/css2?family=Montserrat:wght@400;600;700&display=swap">
<style>
  :root {
    --page-bg: #141414;
    --card-bg: #232323;
    --text-light: #f2f2f2;
    --text-soft: #d9d9d9;
    --teal: #1aa99a;
    --orange: #e8822a;
    --rule: #c9b24a;
  }
  * { margin: 0; padding: 0; box-sizing: border-box; }
  html, body {
    width: 1200px; height: 1059px; overflow: hidden;
    background: var(--page-bg);
    font-family: "Montserrat", Arial, sans-serif;
  }
  .canvas { position: relative; width: 1200px; height: 1059px; }
  .card {
    position: absolute; left: 255px; width: 690px; height: 392px;
    background: var(--card-bg); border-radius: 18px; overflow: hidden;
  }
  .card--front { top: 89px; }
  .card--back { top: 546px; }

  .brand { position: absolute; display: flex; align-items: center; }
  .brand__mark { background: var(--orange); flex: none; }
  .brand__name { color: var(--text-light); font-weight: 600; letter-spacing: -0.5px; line-height: 1; }
  .brand__tagline {
    position: absolute; right: 0; color: var(--text-light);
    font-weight: 700; text-transform: uppercase; white-space: nowrap;
  }

  .card--front .brand { left: 42px; top: 52px; }
  .card--front .brand__mark { width: 26px; height: 26px; margin-right: 10px; }
  .card--front .brand__name { font-size: 36px; }
  .card--front .brand__tagline { top: 40px; font-size: 5.5px; letter-spacing: 0.2px; }

  .card--back .brand { left: 50%; top: 160px; transform: translateX(-50%); }
  .card--back .brand__mark { width: 40px; height: 40px; margin-right: 16px; }
  .card--back .brand__name { font-size: 56px; }
  .card--back .brand__tagline { top: 62px; font-size: 8.5px; letter-spacing: 0.3px; }

  .contact { position: absolute; left: 360px; top: 200px; }
  .contact__name { font-size: 23px; font-weight: 700; letter-spacing: 1px; white-space: nowrap; }
  .contact__first { color: var(--teal); }
  .contact__last { color: var(--orange); }
  .contact__title { color: var(--text-soft); font-size: 16px; margin-top: 2px; }
  .contact__rule { width: 12px; height: 1px; background: var(--rule); margin: 20px 0 14px; }
  .contact__list { list-style: none; }
  .contact__item {
    display: flex; align-items: center; color: var(--text-soft);
    font-size: 15px; letter-spacing: 0.4px; height: 28px; white-space: nowrap;
  }
  .contact__icon { width: 12px; height: 12px; margin-right: 7px; fill: var(--orange); flex: none; }
</style>
</head>
<body>
<div class="canvas">

  <section class="card card--front">
    <div class="brand">
      <span class="brand__mark"></span>
      <span class="brand__name">BrightwellLabs</span>
      <span class="brand__tagline">A Division of Brightwell Civic</span>
    </div>

    <div class="contact">
      <h1 class="contact__name"><span class="contact__first">MARTIN</span> <span class="contact__last">QUELBROOK</span></h1>
      <p class="contact__title">CEO</p>
      <div class="contact__rule"></div>
      <ul class="contact__list">
        <li class="contact__item">
          <svg class="contact__icon" viewBox="0 0 12 12" aria-hidden="true"><path d="M1 4.5C1 2.5 3 1.5 6 1.5s5 1 5 3v1H8.5V4.2C7.8 3.9 4.2 3.9 3.5 4.2v1.3H1z M2.5 6.5h7l1 4h-9z"/></svg>
          555-218-9403
        </li>
        <li class="contact__item">
          <svg class="contact__icon" viewBox="0 0 12 12" aria-hidden="true"><path d="M0.5 5 6 1l5.5 4v6.5h-11z M1.5 5.6 6 8.6l4.5-3L6 2.3z" fill-rule="evenodd"/></svg>
          martin@brightwellcivic.example
        </li>
        <li class="contact__item">
          <svg class="contact__icon" viewBox="0 0 12 12" aria-hidden="true"><circle cx="6" cy="6" r="5.5"/><path d="M3 3.5c1 .2 1.5 1 1.2 2 .8.4 1 1.3.6 2.2M8 2.5c-.6.8-.2 1.6.6 1.8M7.5 8.5c.6-.6 1.5-.5 2 0" stroke="#232323" stroke-width="1" fill="none"/></svg>
          www.brightwellcivic.example
        </li>
      </ul>
    </div>
  </section>

  <section class="card card--back">
    <div class="brand">
      <span class="brand__mark"></span>
      <span class="brand__name">BrightwellLabs</span>
      <span class="brand__tagline">A Division of Brightwell Civic</span>
    </div>
  </section>

</div>
</body>
</html>
```